swimming pool Leak Detection Brochure

I would Like to create a pool leak detection brochure

Target Market(s)

High end Clients with inground swimming pools

Industry/Entity Type

Pool Service

Font styles to use
Other font styles liked:
• Im open to suggestions but using my website for ideas is suggested

Colors

Designer to choose colors to be used in the design.

Requirements
Must have
• Do you Have a Leak??
• Figuring out when your pool has a leak can be tough. Environmental factors do play a role in the water level, and just because your pool’s water is lower than normal does not mean it has a leak. Wind, humidity, and sun exposure all impact your rate of evaporation.
• Warning Signs of a Leak in Your Pool
• Your pool, fountain, or spa loses more than 1/4 an inch of water a day
• There are cracks in or around the pool decking
• You need to add water more than once a week
• Grass around the area is soggy
• Your pool deck is sinking or lifting
Nice to have
• PREPARING FOR A LEAK TEST
• To ensure you receive an accurate leak detection test, it is required that you have the pool vacuumed and cleaned beforehand. Dirt and debris in the pool can make it difficult to spot even large leaks. Likewise, the water should be as clear as possible. If your water is green it means mildew, algae, or fungi has infested it. Not only does this make it impossible to test for leaks, but it’s dangerous for our health. Finally our pool should be full to the normal level - we can’t find a leak that is not leaking! After your test, you will be confident knowing you have a pool/fountain/spa that is free of leaks or the Leak has been found and can be repaired Properly.

```html
<!DOCTYPE html>
<html lang="en">
<head>
<meta charset="utf-8">
<title>Harbor Pool Service – Leak Detection Brochure</title>
<link rel="stylesheet" href="https://fonts.googleapis.com/css2?family=Oswald:wght@500;700&family=Open+Sans:ital,wght@0,400;0,600;0,700;1,400&family=Raleway:wght@500;700&display=swap">
<style>
:root{
  --navy:#0d1b33;
  --navy-2:#13264a;
  --blue:#1f6fc0;
  --sky:#3ea9e6;
  --aqua:#7fd3f5;
  --orange:#f0752a;
  --orange-2:#f39a34;
  --white:#ffffff;
  --ink:#26374f;
  --grey:#5c6b7f;
  --page:#ffffff;
}
*{box-sizing:border-box;margin:0;padding:0}
html,body{width:880px;height:1200px;overflow:hidden;background:var(--page)}
body{font-family:"Open Sans",Arial,sans-serif;color:var(--ink);position:relative}
.spread{position:absolute;left:0;width:880px;display:flex;box-shadow:0 2px 8px rgba(0,0,0,.18)}
.spread--outside{top:15px;height:540px}
.spread--inside{top:585px;height:590px}
.panel{position:relative;width:440px;height:100%;overflow:hidden}

/* outside left */
.photo{position:absolute}
.photo--pool-water{left:0;top:0;width:440px;height:310px;background:linear-gradient(160deg,#8ad8f4 0%,#2c93d6 55%,#1462ad 100%)}
.testimonial{position:absolute;left:50px;top:22px;width:340px;padding:16px 20px;background:rgba(13,27,51,.72);color:var(--white);font-size:9.5px;line-height:1.5;font-style:italic;border-radius:4px}
.testimonial .stars{color:var(--orange-2);font-style:normal;font-size:12px;letter-spacing:2px;margin-bottom:4px}
.testimonial .author{text-align:right;font-style:normal;font-weight:700;margin-top:6px;font-size:10px}
.wave{position:absolute;left:0;width:440px}
.contact{position:absolute;right:28px;top:345px;text-align:right;font-size:9.5px;line-height:1.6;color:var(--ink)}
.contact h3{font-family:"Oswald",sans-serif;color:var(--orange);font-size:15px;letter-spacing:.5px}
.badges{position:absolute;left:30px;top:348px;display:flex;gap:10px}
.badge{width:46px;height:46px;border-radius:50%;background:#d9e6f2;border:3px solid var(--blue)}
.phone-bar{position:absolute;left:0;top:462px;width:440px;height:44px;background:var(--orange);display:flex;align-items:center;justify-content:center;gap:10px;color:var(--white);font-family:"Oswald",sans-serif;font-size:24px;font-weight:700;letter-spacing:.5px}
.site-line{position:absolute;left:0;top:512px;width:440px;text-align:center;font-size:10px;font-weight:600;color:var(--navy)}

/* outside right */
.photo--float{left:0;top:0;width:440px;height:300px;background:radial-gradient(circle at 55% 40%,#f5d046 0 18%,transparent 19%),linear-gradient(170deg,#9fe0f6 0%,#3aa6e2 60%,#1a6fbf 100%)}
.brand{position:absolute;left:50%;top:258px;transform:translateX(-50%);display:flex;align-items:center;gap:8px;background:var(--white);padding:12px 18px;border-radius:40px;box-shadow:0 2px 6px rgba(0,0,0,.2)}
.brand .dot{width:16px;height:16px;border-radius:50%;background:var(--orange)}
.brand .name{font-family:"Oswald",sans-serif;font-weight:700;font-size:18px;color:var(--blue);letter-spacing:.5px}
.tagline{position:absolute;right:40px;top:380px;width:230px;font-family:"Raleway",sans-serif;font-weight:500;color:var(--blue);font-size:22px;line-height:1.25}
.site-bar{position:absolute;left:0;bottom:0;width:440px;height:36px;background:var(--blue);color:var(--white);font-size:11px;font-weight:600;display:flex;align-items:center;justify-content:flex-end;padding-right:26px}

/* inside left */
.panel--leak{background:var(--navy);color:var(--white)}
.leak-body{position:absolute;left:26px;top:72px;width:390px}
.heading-orange{font-family:"Oswald",sans-serif;font-style:italic;font-weight:700;color:var(--orange);text-transform:uppercase;letter-spacing:.5px}
.leak-body h2{font-size:22px;margin-bottom:6px}
.leak-body p{font-size:9.5px;line-height:1.5;margin-bottom:7px}
.leak-body h4{font-size:10px;font-weight:700;margin-bottom:3px}
.leak-body ul{list-style:none;font-size:9.5px;line-height:1.55;margin-bottom:12px}
.leak-body li::before{content:"• ";color:var(--orange)}
.leak-body h2.second{font-size:19px;margin-top:4px}
.partners{position:absolute;left:0;top:452px;width:440px;height:78px;background:var(--white);display:flex;align-items:center;padding:0 16px;gap:10px}
.partner-col{display:flex;flex-direction:column;gap:6px}
.partner{width:62px;height:16px;border-radius:3px;background:#c9d3de}
.partner--alt{background:#e7b8a0}
.photo--equipment{position:relative;width:120px;height:60px;background:linear-gradient(135deg,#2a3a55,#5f7594);border-radius:4px}
.phone-line{position:absolute;left:0;bottom:14px;width:440px;display:flex;align-items:center;justify-content:center;gap:10px;font-family:"Oswald",sans-serif;font-size:22px;font-weight:700}

/* inside right */
.panel--services{background:var(--white)}
.services-body{position:absolute;left:26px;top:34px;width:390px}
.services-body h2{font-size:21px;line-height:1.2;margin-bottom:10px}
.services-body h3{font-family:"Oswald",sans-serif;color:var(--blue);font-size:14px;margin-bottom:4px}
.services-body h3 small{font-size:9px;color:var(--grey);font-family:"Open Sans",sans-serif}
.services-body p{font-size:9.5px;line-height:1.55;color:var(--grey);margin-bottom:9px}
.services-body h4{font-size:12px;color:var(--blue);margin:4px 0 4px}
.guarantee{font-size:10px;line-height:1.5;color:var(--orange);font-weight:700}
</style>
</head>
<body>

<section class="spread spread--outside">
  <div class="panel panel--back">
    <div class="photo photo--pool-water" role="img" aria-label="Photo of clear blue swimming pool water"></div>
    <blockquote class="testimonial">
      <div class="stars">★★★★★</div>
      “The crew found the leak in our pool within a single visit and explained every step. Repairs were quick, the deck was left spotless, and our water level has held steady all summer. Highly recommended for any pool owner.”
      <div class="author">Daniel R.</div>
    </blockquote>
    <svg class="wave" style="top:240px" width="440" height="110" viewBox="0 0 440 110" aria-hidden="true">
      <path d="M0 40 C120 0 260 90 440 20 L440 110 L0 110 Z" fill="var(--orange)"/>
      <path d="M0 70 C140 30 280 110 440 55 L440 110 L0 110 Z" fill="var(--white)"/>
    </svg>
    <div class="badges">
      <div class="badge"></div><div class="badge"></div><div class="badge"></div>
    </div>
    <div class="contact">
      <h3>CONTACT US</h3>
      Harbor Pool Service<br>
      PO Box 4417<br>
      Warwick, RI 02886<br>
      info@harborpoolcare.com
    </div>
    <div class="phone-bar">
      <svg width="20" height="20" viewBox="0 0 24 24" aria-hidden="true"><path fill="#fff" d="M6.6 10.8a15 15 0 0 0 6.6 6.6l2.2-2.2c.3-.3.7-.4 1-.2 1.1.4 2.3.6 3.6.6.6 0 1 .4 1 1V20c0 .6-.4 1-1 1A17 17 0 0 1 3 4c0-.6.4-1 1-1h3.5c.6 0 1 .4 1 1 0 1.3.2 2.5.6 3.6.1.3 0 .7-.2 1z"/></svg>
      401-555-0172
    </div>
    <div class="site-line">www.harborpoolcare.com</div>
  </div>

  <div class="panel panel--cover">
    <div class="photo photo--float" role="img" aria-label="Photo of a child relaxing on a yellow float in a blue pool"></div>
    <svg class="wave" style="top:270px" width="440" height="120" viewBox="0 0 440 120" aria-hidden="true">
      <path d="M0 30 C150 80 300 0 440 40 L440 120 L0 120 Z" fill="var(--orange)"/>
      <path d="M0 50 C150 100 300 20 440 60 L440 120 L0 120 Z" fill="var(--blue)"/>
      <path d="M0 70 C150 120 300 40 440 82 L440 120 L0 120 Z" fill="var(--white)"/>
    </svg>
    <div class="brand"><span class="dot"></span><span class="name">HARBOR POOL SERVICE</span></div>
    <div class="tagline">Dive Into<br>Professional Pool<br>Service &amp; Repair</div>
    <div class="site-bar">www.harborpoolcare.com</div>
  </div>
</section>

<section class="spread spread--inside">
  <div class="panel panel--leak">
    <svg class="wave" style="top:0" width="440" height="60" viewBox="0 0 440 60" aria-hidden="true">
      <path d="M0 0 H440 V30 C300 60 150 10 0 40 Z" fill="var(--blue)"/>
      <path d="M0 0 H440 V16 C300 44 150 0 0 24 Z" fill="var(--sky)"/>
    </svg>
    <div class="leak-body">
      <h2 class="heading-orange">Do You Have a Leak??</h2>
      <p>Figuring out when your pool has a leak can be tough. Environmental factors do play a role in the water level, and just because your pool’s water is lower than normal does not mean it has a leak. Wind, humidity, and sun exposure all impact your rate of evaporation.</p>
      <h4>Warning Signs of a Leak in Your Pool</h4>
      <ul>
        <li>Your pool, fountain, or spa loses more than 1/4 an inch of water a day</li>
        <li>There are cracks in or around the pool decking</li>
        <li>You need to add water more than once a week</li>
        <li>Grass around the area is soggy</li>
        <li>Your pool deck is sinking or lifting</li>
      </ul>
      <h2 class="heading-orange second">Preparing for a Leak Test</h2>
      <p>To ensure you receive an accurate leak detection test, it is required that you have the pool vacuumed and cleaned beforehand. Dirt and debris in the pool can make it difficult to spot even large leaks. Likewise, the water should be as clear as possible. If your water is green it means mildew, algae, or fungi has infested it. Not only does this make it impossible to test for leaks, but it’s dangerous for our health. Finally our pool should be full to the normal level - we can’t find a leak that is not leaking! After your test, you will be confident knowing you have a pool/fountain/spa that is free of leaks or the Leak has been found and can be repaired Properly.</p>
    </div>
    <div class="partners">
      <div class="partner-col"><div class="partner"></div><div class="partner partner--alt"></div></div>
      <div class="photo photo--equipment" role="img" aria-label="Photo of pool pumps and filtration equipment"></div>
      <div class="partner-col"><div class="partner"></div><div class="partner"></div></div>
      <div class="partner-col"><div class="partner partner--alt"></div><div class="partner"></div></div>
    </div>
    <div class="phone-line">
      <svg width="20" height="20" viewBox="0 0 24 24" aria-hidden="true"><path fill="var(--orange)" d="M6.6 10.8a15 15 0 0 0 6.6 6.6l2.2-2.2c.3-.3.7-.4 1-.2 1.1.4 2.3.6 3.6.6.6 0 1 .4 1 1V20c0 .6-.4 1-1 1A17 17 0 0 1 3 4c0-.6.4-1 1-1h3.5c.6 0 1 .4 1 1 0 1.3.2 2.5.6 3.6.1.3 0 .7-.2 1z"/></svg>
      401-555-0172
    </div>
  </div>

  <div class="panel panel--services">
    <div class="services-body">
      <h2 class="heading-orange">Pool Maintenance,<br>Cleaning, &amp; Repairs in RI</h2>
      <h3>HARBOR POOL SERVICE <small>RI, MA, CT</small></h3>
      <p>Serving homeowners across the region, we provide weekly maintenance, seasonal openings and closings, equipment upgrades and precise leak detection. Our trained technicians treat every backyard with care, arrive on schedule and leave each pool clean, balanced and ready to enjoy. From small repairs to complete renovations, we handle it all.</p>
      <p>We use modern listening gear, pressure testing and dye tests to locate leaks in shells, plumbing lines, lights and skimmers. Once found, we explain the options clearly and complete lasting repairs with quality parts from trusted manufacturers.</p>
      <h4>Benefits of Harbor Pool Service</h4>
      <p>As a family owned and operated local business, we stand behind every job. Our crew is fully licensed and insured, communicates promptly and keeps your property tidy. Clients count on honest pricing, thorough work and reliable follow-up long after the visit is done.</p>
      <p>We have been trusted by high-end homeowners for years and take pride in protecting their investment season after season with attentive, professional service.</p>
      <p class="guarantee">Your satisfaction is GUARANTEED.<br>For Pool Repair, Maintenance, and Cleaning<br>Call Harbor Pool Service TODAY!</p>
    </div>
    <svg class="wave" style="bottom:0" width="440" height="70" viewBox="0 0 440 70" aria-hidden="true">
      <path d="M0 30 C150 0 300 60 440 20 V70 H0 Z" fill="var(--sky)"/>
      <path d="M0 46 C150 16 300 76 440 38 V70 H0 Z" fill="var(--blue)"/>
    </svg>
  </div>
</section>

</body>
</html>
```